Modern Business Card for Larkwell 2018

Our company assumes the best about people. We are creating an online community of entrepreneurs and business leaders who struggle with marketing their business online.

This business card should POP! We recently got a new logo and are launching a new website next month, so our business cards should make a statement that feels:
-Fresh
-Smart
-Trustworthy
-Fun

Target Market(s)

small business owners, entrepreneurs

Industry/Entity Type

Digital Marketing

Contact Information for Business Card

Dimensions: 3.5" x 2"

Font styles to use
Sans Serif

Colors
f37122
ffffff

Requirements
Must have
• We need a business card with a modern, bold design. We will use one side of the card as a lead-generation offer, so text on one side will need to fit up to 140 characters. The business card should stick to our core colors (orange, black, and white).
Nice to have
• We think a vertical "portrait" design could be interesting.
Should not have
• Should not look like a traditional business card. The round icon should stand out from a distance.

```html
<!DOCTYPE html>
<html lang="en">
<head>
<meta charset="utf-8">
<title>Larkwell Business Card</title>
<link rel="stylesheet" href="https://fonts.googleapis.com/css2?family=Roboto:wght@400;700;900&family=Roboto+Condensed:wght@400;500;700&display=swap">
<style>
  :root {
    --orange: #e05a22;
    --paper: #efefef;
    --ink: #1c1c1c;
    --white: #ffffff;
    --backdrop: #3b3b3b;
    --rule: #555555;
  }
  * { margin: 0; padding: 0; box-sizing: border-box; }
  html, body { width: 1200px; height: 751px; overflow: hidden; }
  body { background: var(--backdrop); font-family: "Roboto", sans-serif; position: relative; }

  .card { position: absolute; top: 219px; width: 492px; height: 280px; background: var(--paper); overflow: hidden; }
  .card--front { left: 91px; }
  .card--back { left: 620px; }

  .wordmark { position: absolute; font-family: "Roboto", sans-serif; font-weight: 900; letter-spacing: 1px; white-space: nowrap; line-height: 1; }
  .tagline { position: absolute; font-family: "Roboto Condensed", sans-serif; font-weight: 700; text-transform: uppercase; letter-spacing: 0.6px; white-space: nowrap; line-height: 1; }

  .card--front .wordmark { left: 0; width: 492px; text-align: center; top: 60px; font-size: 36px; color: var(--ink); }
  .card--front .tagline { left: 0; width: 492px; text-align: center; top: 99px; font-size: 12px; color: var(--ink); }

  .contact-band { position: absolute; left: 0; top: 178px; width: 492px; height: 84px; background: var(--orange); }
  .badge-circle { position: absolute; left: -1px; top: 176px; width: 90px; height: 90px; border-radius: 50%; background: var(--orange); border: 5px solid var(--paper); }
  .contact { position: absolute; left: 130px; width: 234px; top: 188px; text-align: center; color: var(--white); }
  .contact__name { font-family: "Roboto Condensed", sans-serif; font-weight: 500; font-size: 21px; line-height: 24px; letter-spacing: 0.3px; }
  .contact__title { font-family: "Roboto Condensed", sans-serif; font-size: 13.5px; line-height: 17px; }
  .contact__email { font-size: 12px; line-height: 16px; }

  .offer-panel { position: absolute; left: 0; top: 0; width: 492px; height: 178px; background: var(--orange); }
  .footer-strip { position: absolute; left: 0; top: 262px; width: 492px; height: 18px; background: var(--orange); }

  .back-mark { position: absolute; left: 115px; top: 46px; width: 32px; height: 32px; border-radius: 50%; background: var(--white); }
  .card--back .wordmark { left: 0; width: 262px; text-align: center; top: 92px; font-size: 29px; color: var(--white); }
  .card--back .tagline { left: 0; width: 262px; text-align: center; top: 123px; font-size: 9.5px; color: var(--white); }
  .divider { position: absolute; left: 244px; top: 22px; width: 1px; height: 134px; background: rgba(255,255,255,0.55); }

  .offer { position: absolute; left: 265px; top: 23px; color: var(--white); }
  .offer__headline { font-family: "Roboto Condensed", sans-serif; font-weight: 700; font-size: 17.5px; line-height: 17px; text-transform: uppercase; }
  .offer__body { margin-top: 5px; font-size: 13px; line-height: 16.5px; }
  .offer__link { margin-top: 6px; font-family: "Roboto Condensed", sans-serif; font-weight: 700; font-size: 16.5px; }

  .write-line { position: absolute; left: 42px; width: 409px; height: 1px; background: var(--rule); }
  .write-line--1 { top: 204px; }
  .write-line--2 { top: 237px; }
</style>
</head>
<body>
  <section class="card card--front">
    <div class="wordmark">LARKWELL</div>
    <div class="tagline">Tell stories that inspire action</div>
    <div class="contact-band"></div>
    <div class="badge-circle"></div>
    <div class="contact">
      <div class="contact__name">DANA WHITFIELD</div>
      <div class="contact__title">STORY MARKETING COACH</div>
      <div class="contact__email">dana@larkwellnow.com</div>
    </div>
  </section>

  <section class="card card--back">
    <div class="offer-panel"></div>
    <div class="back-mark"></div>
    <div class="wordmark">LARKWELL</div>
    <div class="tagline">Tell stories that inspire action</div>
    <div class="divider"></div>
    <div class="offer">
      <div class="offer__headline">Reach more people.<br>Make more money.<br>Create more impact.</div>
      <div class="offer__body">Get your free Larkwell<br>Starter Package and our<br>marketing guide today at</div>
      <div class="offer__link">Larkwellnow.com/start</div>
    </div>
    <div class="write-line write-line--1"></div>
    <div class="write-line write-line--2"></div>
    <div class="footer-strip"></div>
  </section>
</body>
</html>
```